German Headhunter/ HR Consultancy needs Business Cards Design

We need a business Card Design for our Company in Stuttgart. We are specialized as Headhunter/ HR Consultancy in Placement of specialist and managers in permanent employment. Please refer to our business logo.

```html
<!DOCTYPE html>
<html lang="de">
<head>
<meta charset="utf-8">
<title>Vantora Personalberatung – Business Card</title>
<link href="https://fonts.googleapis.com/css2?family=Montserrat:wght@500;600;700&family=Arimo:wght@400&display=swap" rel="stylesheet">
<style>
  :root{
    --stage:#cfcfcf;
    --card-dark:#232323;
    --brand-blue:#3a53c4;
    --brand-blue-deep:#2c40a8;
    --pattern-blue:#2f45ad;
    --text-grey:#b9b9b9;
    --rule-grey:#5a5a5a;
    --white:#ffffff;
  }
  *{box-sizing:border-box;margin:0;padding:0}
  html,body{width:1200px;height:800px;overflow:hidden}
  body{
    background:var(--stage);
    display:flex;align-items:center;justify-content:center;gap:44px;
    font-family:"Arimo",Arial,sans-serif;
  }
  .card{
    position:relative;width:540px;height:309px;
    box-shadow:0 14px 30px rgba(0,0,0,.28);
    overflow:hidden;
  }
  .card--front{background:var(--card-dark);border-bottom:3px solid var(--brand-blue)}
  .brand{
    position:absolute;display:flex;align-items:center;gap:12px;
    font-family:"Montserrat",sans-serif;font-weight:600;text-transform:uppercase;
  }
  .brand__mark{width:34px;height:34px;background:currentColor;flex:none}
  .brand__name{line-height:1.15}
  .brand__name span{display:block}
  .brand__name .primary{font-size:30px;letter-spacing:1px}
  .brand__name .secondary{font-size:12.5px;letter-spacing:1.6px}
  .card--front .brand{left:190px;top:46px;color:var(--brand-blue)}
  .person{position:absolute;left:34px;top:120px}
  .person__name{font-family:"Montserrat",sans-serif;font-weight:600;font-size:20px;color:var(--brand-blue);letter-spacing:.5px}
  .person__role{font-size:15px;color:var(--text-grey);margin-top:2px}
  .rule{position:absolute;left:28px;right:28px;top:168px;height:1px;background:var(--rule-grey)}
  .contacts{position:absolute;left:34px;top:186px;list-style:none;color:var(--text-grey);font-size:15px}
  .contacts li{display:flex;align-items:center;gap:9px;margin-bottom:6px;line-height:17px}
  .contacts svg{width:15px;height:15px;flex:none}
  .contacts .accent{color:var(--brand-blue)}
  .address{position:absolute;right:34px;top:186px;text-align:right;color:var(--text-grey);font-size:15px;line-height:23px}
  .card--back{background:var(--brand-blue)}
  .pattern{
    position:absolute;inset:0;
    background:linear-gradient(135deg,var(--brand-blue) 0%,var(--pattern-blue) 60%,var(--brand-blue-deep) 100%);
  }
  .card--back .brand{left:118px;top:120px;color:var(--white)}
  .card--back .brand__name .primary{font-size:32px}
</style>
</head>
<body>
  <section class="card card--front" aria-label="Business card front">
    <div class="brand">
      <span class="brand__mark"></span>
      <div class="brand__name"><span class="primary">Vantora</span><span class="secondary">Personalberatung</span></div>
    </div>
    <div class="person">
      <p class="person__name">LUKAS BERGER</p>
      <p class="person__role">Managing Director</p>
    </div>
    <div class="rule"></div>
    <ul class="contacts">
      <li><svg viewBox="0 0 24 24" fill="var(--brand-blue)"><path d="M6.6 10.8a15 15 0 0 0 6.6 6.6l2.2-2.2c.3-.3.7-.4 1-.2 1.1.4 2.3.6 3.6.6.6 0 1 .4 1 1V20c0 .6-.4 1-1 1A17 17 0 0 1 3 4c0-.6.4-1 1-1h3.5c.6 0 1 .4 1 1 0 1.3.2 2.5.6 3.6.1.3 0 .7-.2 1z"/></svg><span>044-987 654 321</span></li>
      <li><svg viewBox="0 0 24 24" fill="var(--brand-blue)"><path d="M2 5h20v14H2z"/><path d="M2 5l10 8 10-8" fill="none" stroke="var(--card-dark)" stroke-width="2"/></svg><span>info@vantora-hr.com</span></li>
      <li><svg viewBox="0 0 24 24" fill="none" stroke="var(--brand-blue)" stroke-width="2"><circle cx="12" cy="12" r="9"/><path d="M3 12h18M12 3c3 3 3 15 0 18M12 3c-3 3-3 15 0 18"/></svg><span>www.<span class="accent">vantora-hr</span>.com</span></li>
    </ul>
    <p class="address">58, Lindenhof Straße<br>70469, Germany</p>
  </section>

  <section class="card card--back" aria-label="Business card back">
    <div class="pattern" role="img" aria-label="Embossed repeating brand pattern in tonal blue"></div>
    <div class="brand">
      <span class="brand__mark"></span>
      <div class="brand__name"><span class="primary">Vantora</span><span class="secondary">Personalberatung</span></div>
    </div>
  </section>
</body>
</html>
```